Business Card Design Project

The logo I included in my order was a previous image that we've used for shirts, signs, magnets, etc. We've decided to go back to that logo, with some updates.
We need to add "Inc." after "Dunmore Roofing,"
Also, I need the logo with a transparent background so that I can use it on other projects.

The business cards will be the first item I order with the new logo. The employee's info is:
Glenn Parry
Sales Manager
484-610-3357
gparry@dunmoreroofinginc.example

Also, I want a "Find us on Chatterly" icon on the card, along with our web address, www.dunmoreroofinginc.example.

Any questions, please email or call me:
lindadunmore@mailbox.example
484-729-1186

Reason: This is the first time I've tried Pixel Forum.

My timetable changed and I need to select a design by the end of the work day, 6 hours from now.Thanks so much for all of the super designs.

Target Market(s)

Homeowners

Industry/Entity Type

Business

Font styles to use
Serif

Requirements
Must have
• Transparent background
Similar to logo in photo I sent you

```html
<!DOCTYPE html>
<html lang="en">
<head>
<meta charset="utf-8">
<title>Dunmore Roofing Inc. — Business Card</title>
<link rel="stylesheet" href="https://fonts.googleapis.com/css2?family=Cinzel:wght@400;700&family=Cormorant+Garamond:wght@500&display=swap">
<style>
  :root {
    --backdrop: #2a2420;
    --card-dark: #1c1c1c;
    --card-glow: #3a3a3a;
    --lime: #b8b84a;
    --lime-light: #e6e8a0;
    --logo-lime: #d8d88c;
    --ink-light: #f2f2f2;
    --ink-dark: #2a2a1c;
  }
  * { margin: 0; padding: 0; box-sizing: border-box; }
  html, body {
    width: 1200px; height: 1000px; overflow: hidden;
    background: var(--backdrop);
  }
  .card {
    position: absolute; left: 351px; top: 62px;
    width: 498px; height: 870px;
    background: radial-gradient(ellipse at 50% 30%, var(--card-glow) 0%, var(--card-dark) 65%);
    overflow: hidden;
    font-family: "Cinzel", serif;
    color: var(--ink-light);
    text-align: center;
  }
  .company-mark {
    position: absolute; left: 0; right: 0; top: 248px;
    display: flex; align-items: center; justify-content: center; gap: 14px;
    color: var(--logo-lime);
    font-family: "Cinzel", serif; font-weight: 700;
    font-size: 34px; line-height: 1.05; letter-spacing: 1px;
  }
  .company-mark .mark-square {
    width: 22px; height: 22px; background: var(--logo-lime); flex: none;
  }
  .company-mark .mark-name { text-align: left; }
  .person-name {
    position: absolute; left: 0; right: 0; top: 388px;
    font-size: 44px; font-weight: 400;
    text-shadow: 2px 3px 3px rgba(0,0,0,0.9);
  }
  .person-title {
    position: absolute; left: 0; right: 0; top: 458px;
    font-family: "Cormorant Garamond", serif; font-weight: 500;
    font-size: 21px; letter-spacing: 0.5px;
  }
  .person-phone {
    position: absolute; left: 0; right: 0; top: 480px;
    font-family: "Cormorant Garamond", serif; font-weight: 500;
    font-size: 38px;
  }
  .person-email {
    position: absolute; left: 0; right: 0; top: 527px;
    font-size: 17px; white-space: nowrap;
  }
  .domain-suffix { font-size: 0.72em; }
  .contact-band {
    position: absolute; left: 0; right: 0; bottom: 0; height: 161px;
    background: var(--lime);
    border-top: 3px solid var(--lime-light);
    color: var(--ink-dark);
  }
  .office-phone {
    position: absolute; right: 20px; top: 54px;
    font-family: "Cormorant Garamond", serif; font-weight: 500;
    font-size: 38px;
  }
  .office-web {
    position: absolute; right: 20px; top: 106px;
    font-size: 20px; white-space: nowrap;
  }
  .social-link {
    position: absolute; left: 20px; top: 100px;
    display: flex; align-items: center; gap: 8px;
    font-family: "Cinzel", serif; font-weight: 700;
    font-size: 11px; line-height: 1.15; text-align: left;
    color: var(--ink-dark);
  }
  .social-link .social-square { width: 14px; height: 30px; background: var(--ink-dark); flex: none; }
  .social-link .social-name { font-size: 15px; display: block; }
</style>
</head>
<body>
  <section class="card">
    <div class="company-mark">
      <span class="mark-square"></span>
      <span class="mark-name">Dunmore<br>Roofing Inc.</span>
    </div>

    <h1 class="person-name">Glenn Parry</h1>
    <p class="person-title">SALES MANAGER</p>
    <p class="person-phone">(484) 610-3357</p>
    <p class="person-email">gParry@DunmoreRoofingInc<span class="domain-suffix">.example</span></p>

    <footer class="contact-band">
      <div class="social-link">
        <span class="social-square"></span>
        <span>Find us on:<span class="social-name">Chatterly</span></span>
      </div>
      <p class="office-phone">(610) 847-2291</p>
      <p class="office-web">DunmoreRoofingInc<span class="domain-suffix">.example</span></p>
    </footer>
  </section>
</body>
</html>
```